RWT Fittings Ltd Business Cards

We need a business card with our business logo. We provide window and door installations on high-rises in west coast British Colombia, Canada.

I would like my business information and details on one side of the card, and the other side the company name with logo

Target Market(s)

General Contractors

Industry/Entity Type

Construction

Contact Information for Business Card

one side i want my company name and logo in the dark theme logo that i provided

Requirements
Must have
• Marco Peltieri, 16045518293, RWTFittings@mailbox-demo.com, 1407-5194 Linden Row Burnaby BC, V5H 2K9, Owner & Manager

```html
<!DOCTYPE html>
<html lang="en">
<head>
<meta charset="utf-8">
<title>RWT Fittings Ltd Business Cards</title>
<link rel="stylesheet" href="https://fonts.googleapis.com/css2?family=Open+Sans:wght@400;600;700&display=swap">
<style>
  :root {
    --backdrop: #262626;
    --card: #212125;
    --accent: #29abe2;
    --grey: #9a9a9a;
    --white: #ffffff;
  }
  * { margin: 0; padding: 0; box-sizing: border-box; }
  html, body { width: 1200px; height: 780px; overflow: hidden; }
  body {
    background: var(--backdrop);
    font-family: "Open Sans", Arial, sans-serif;
    position: relative;
  }
  .card {
    position: absolute;
    width: 560px;
    height: 320px;
    background: var(--card);
    box-shadow: 0 10px 30px rgba(0,0,0,.55);
    overflow: hidden;
  }
  .card--front { left: 70px; top: 60px; }
  .card--back { left: 570px; top: 400px; }

  .edge-band {
    position: absolute;
    width: 10px;
    background: var(--accent);
  }
  .edge-band--left { left: 0; bottom: 26px; height: 150px; }
  .edge-band--right { right: 0; top: 26px; height: 150px; }

  .wordmark {
    display: flex;
    align-items: center;
    gap: 14px;
    color: var(--accent);
    font-weight: 700;
    white-space: nowrap;
  }
  .wordmark__square {
    background: var(--grey);
    flex: none;
  }
  .card--front .wordmark {
    position: absolute;
    left: 0; right: 0; top: 0; bottom: 0;
    justify-content: center;
    font-size: 40px;
    letter-spacing: .5px;
  }
  .card--front .wordmark__square { width: 40px; height: 40px; }

  .card--back .wordmark {
    position: absolute;
    left: 40px;
    top: 132px;
    font-size: 21px;
    gap: 10px;
  }
  .card--back .wordmark__square { width: 22px; height: 22px; }

  .divider {
    position: absolute;
    left: 262px;
    top: 50px;
    width: 2px;
    height: 180px;
    background: linear-gradient(to bottom, rgba(255,255,255,0), var(--white) 50%, rgba(255,255,255,0));
  }

  .contact {
    position: absolute;
    left: 290px;
    top: 52px;
    color: var(--white);
  }
  .contact__name {
    font-size: 26px;
    font-weight: 700;
    line-height: 1.1;
    white-space: nowrap;
  }
  .contact__first { color: var(--accent); }
  .contact__last { color: var(--grey); }
  .contact__role {
    font-size: 13px;
    font-weight: 600;
    margin-top: 4px;
  }
  .contact__list {
    list-style: none;
    margin-top: 22px;
    font-size: 12.5px;
  }
  .contact__item {
    display: flex;
    align-items: center;
    gap: 8px;
    margin-bottom: 7px;
    white-space: nowrap;
  }
  .contact__icon { width: 14px; height: 14px; flex: none; }

  .address {
    position: absolute;
    right: 34px;
    bottom: 34px;
    color: var(--white);
    font-size: 14px;
    white-space: nowrap;
  }
</style>
</head>
<body>

  <section class="card card--front" aria-label="Business card front">
    <div class="edge-band edge-band--left"></div>
    <div class="edge-band edge-band--right"></div>
    <div class="wordmark">
      <span class="wordmark__square"></span>
      <span class="wordmark__name">RWT Fittings Ltd</span>
    </div>
  </section>

  <section class="card card--back" aria-label="Business card back">
    <div class="edge-band edge-band--left"></div>
    <div class="edge-band edge-band--right"></div>

    <div class="wordmark">
      <span class="wordmark__square"></span>
      <span class="wordmark__name">RWT Fittings Ltd</span>
    </div>

    <div class="divider"></div>

    <div class="contact">
      <p class="contact__name"><span class="contact__first">Marco</span> <span class="contact__last">Peltieri</span></p>
      <p class="contact__role">Owner &amp; Manager</p>
      <ul class="contact__list">
        <li class="contact__item">
          <svg class="contact__icon" viewBox="0 0 24 24" aria-hidden="true"><path fill="#29abe2" d="M6.6 10.8a15.1 15.1 0 0 0 6.6 6.6l2.2-2.2a1 1 0 0 1 1-.25 11.4 11.4 0 0 0 3.6.57 1 1 0 0 1 1 1V20a1 1 0 0 1-1 1A17 17 0 0 1 3 4a1 1 0 0 1 1-1h3.5a1 1 0 0 1 1 1c0 1.250.2 2.450.57 3.570a1 1 0 0 1-.25 1z"/></svg>
          <span>(604) 551-8293</span>
        </li>
        <li class="contact__item">
          <svg class="contact__icon" viewBox="0 0 24 24" aria-hidden="true"><rect x="2" y="5" width="20" height="14" rx="2" fill="#29abe2"/><path d="M3 6l9 7 9-7" fill="none" stroke="#212125" stroke-width="1.8"/></svg>
          <span>RWTFittings@mailbox-demo.com</span>
        </li>
        <li class="contact__item">
          <svg class="contact__icon" viewBox="0 0 24 24" aria-hidden="true"><circle cx="12" cy="12" r="10" fill="#29abe2"/><path d="M2 12h20M12 2c3 3 3 17 0 20M12 2c-3 3-3 17 0 20" fill="none" stroke="#212125" stroke-width="1.4"/></svg>
          <span>www.rwtfittings-demo.com</span>
        </li>
      </ul>
    </div>

    <p class="address">1407-5194 Linden Row Burnaby BC, V5H 2K9</p>
  </section>

</body>
</html>
```